Harborline marketing postcards (6x9)

I would like to replicate this 6x9 postcard, but update name/logo, phone number, web address, etc. I also need to create a second postcard copying this basic design, but with updated content and background pictures. Updated contact info to be used for both postcards:
Website: www.harborlinerealty.com
Name: Mark Fenwick
Email: mfenwick@harborlinerealty.com
Phone: (555) 246-8013

Requirements
Must have
• Need two 6x9 postcard designs; 1 themed for KV-Lorrin, 1 for Delvar R&K. Have uploaded photos that can be used in design. KV can be used for KV postcard (only), R&K can be used for R&K (only), Generic can be used for either. I've tried to upload extra photos so that you can use your creativity in selecting those that work best in the design.
Nice to have
• In the "Color palette" file, it has the two color schemes -- one for KV-Lorrin and one for Delvar R&K. Those respective color schemes should be heavily represented in each design. Then there are different groups of pictures labelled either "R&K" or "KV", plus some labelled "Generic". The generic ones can be used in either design, the others should be used only for the design for that school.

```html
<!DOCTYPE html>
<html lang="en">
<head>
<meta charset="utf-8">
<title>Harborline Realty Postcards</title>
<link rel="stylesheet" href="https://fonts.googleapis.com/css2?family=PT+Sans:wght@400;700&display=swap">
<style>
  :root {
    --backdrop: #d6d6d6;
    --ink: #111111;
    --dark-1: #4a4a4a;
    --dark-2: #0e0e0e;
    --tan-light: #d3bc9c;
    --tan-mid: #b79a74;
    --tan-dark: #9c7c55;
    --tan-text: #f1e2c8;
    --cream: #fdf6ec;
    --muted-brown: #8a7762;
    --white: #ffffff;
    --photo-green: #5f7f3c;
    --photo-sky: #6e9fd8;
    --photo-water: #4d6f86;
  }
  * { box-sizing: border-box; margin: 0; padding: 0; }
  html, body { width: 1022px; height: 1200px; overflow: hidden; }
  body {
    background: var(--backdrop);
    font-family: "PT Sans", Arial, sans-serif;
    position: relative;
  }
  .postcard {
    position: absolute;
    left: 145px;
    width: 732px;
    height: 487px;
    overflow: hidden;
  }
  .postcard--front { top: 100px; background: var(--dark-2); }
  .postcard--back { top: 637px; background: var(--white); }

  /* Front */
  .front__topbar {
    position: absolute; left: 0; top: 0; width: 100%; height: 58px;
    background: radial-gradient(ellipse at 45% 0%, var(--dark-1), var(--dark-2) 70%);
    border-bottom: 7px solid var(--tan-mid);
    height: 65px;
  }
  .front__photo {
    position: absolute; left: 0; top: 65px; width: 100%; height: 361px;
    background: linear-gradient(180deg, var(--photo-sky) 0%, #9fb9c9 35%, var(--photo-green) 62%, #7d8f55 85%, #b9b7a8 100%);
  }
  .front__bottombar {
    position: absolute; left: 0; top: 426px; width: 100%; height: 61px;
    background: linear-gradient(180deg, #2a2a2a, var(--dark-2));
    border-top: 5px solid var(--tan-mid);
  }
  .front__panel {
    position: absolute; left: 12px; top: 0; width: 228px; height: 487px;
    background: linear-gradient(180deg, var(--tan-light) 0%, var(--tan-mid) 55%, var(--tan-dark) 100%);
    box-shadow: 4px 0 8px rgba(0,0,0,0.35);
  }
  .front__headline {
    position: absolute; left: 14px; top: 96px; width: 210px;
    font-size: 26px; font-weight: 700; line-height: 35px; color: var(--ink);
  }
  .rule {
    position: absolute; height: 3px; width: 105px; background: var(--ink);
  }
  .front__panel .rule { left: 14px; top: 212px; }
  .front__body {
    position: absolute; left: 14px; top: 230px; width: 200px;
    font-size: 16px; line-height: 23px; color: var(--ink);
  }
  .front__cta {
    position: absolute; left: 0; top: 357px; width: 100%; text-align: center;
    font-size: 14px; color: var(--tan-text); letter-spacing: 0.2px;
  }
  .phone-pill {
    position: absolute; left: 12px; top: 384px; width: 206px; height: 30px;
    border-radius: 15px;
    background: linear-gradient(180deg, #3a3a3a, var(--dark-2));
    box-shadow: 0 2px 4px rgba(0,0,0,0.4);
    display: flex; align-items: center; justify-content: center; gap: 12px;
    color: var(--white); font-size: 16px; font-weight: 700;
  }
  .front__name {
    position: absolute; left: 0; top: 425px; width: 100%; text-align: center;
    font-size: 22px; color: var(--tan-text);
  }
  .brand {
    position: absolute; display: flex; align-items: center; gap: 8px;
    font-weight: 700; font-size: 17px; letter-spacing: 0.3px; text-transform: uppercase;
  }
  .brand__mark { width: 22px; height: 22px; }
  .front .brand, .postcard--front .brand { right: 14px; top: 17px; color: var(--white); }
  .postcard--front .brand__mark { background: var(--white); }
  .front__contacts {
    position: absolute; left: 252px; top: 454px; display: flex; gap: 18px;
    color: var(--white); font-size: 14px; font-weight: 700;
  }
  .contact { display: flex; align-items: center; gap: 6px; }
  .icon { width: 13px; height: 13px; flex: none; }

  /* Back */
  .back__design { position: absolute; left: 0; top: 0; width: 372px; height: 487px; }
  .back__photo-student {
    position: absolute; left: 0; top: 0; width: 138px; height: 113px;
    background: linear-gradient(180deg, #c9cdd2, #7f93ad 60%, #4b4f57);
  }
  .back__photo-bridge {
    position: absolute; left: 139px; top: 0; width: 226px; height: 113px;
    background: linear-gradient(180deg, #d7c9b0 0%, #8fa3a6 30%, var(--photo-water) 65%, #3e5a3c 100%);
  }
  .back__banner {
    position: absolute; left: 0; top: 113px; width: 372px; height: 121px;
    background: linear-gradient(180deg, var(--tan-mid), var(--tan-dark));
    box-shadow: 0 4px 8px rgba(0,0,0,0.3);
    padding: 20px 0 0 25px;
    font-size: 21px; font-weight: 700; line-height: 29px; color: var(--ink);
  }
  .back__banner .highlight { color: var(--tan-text); }
  .back__content {
    position: absolute; left: 0; top: 234px; width: 365px; height: 200px;
    background: var(--cream);
  }
  .back__lead {
    position: absolute; left: 25px; top: 12px; width: 320px;
    font-size: 17px; line-height: 24px; color: var(--ink);
  }
  .back__content .rule { left: 25px; top: 72px; }
  .back__note {
    position: absolute; left: 25px; top: 87px; width: 270px;
    font-size: 14px; font-weight: 700; line-height: 17px; color: var(--muted-brown);
  }
  .back__contact-row {
    position: absolute; left: 25px; top: 156px; display: flex; gap: 12px; align-items: center;
    font-size: 12.5px; color: var(--ink);
  }
  .back__contact-row .email { font-weight: 700; }
  .back__footer {
    position: absolute; left: 0; top: 434px; width: 365px; height: 53px;
    background: linear-gradient(180deg, #3a3a3a, var(--dark-2));
  }
  .back__footer-web {
    position: absolute; left: 0; top: 26px; width: 100%; text-align: center;
    color: var(--white); font-size: 14px; font-weight: 700;
  }
  .name-pill {
    position: absolute; left: 30px; top: 421px; width: 316px; height: 30px;
    border-radius: 15px; background: var(--tan-light);
    box-shadow: 0 3px 5px rgba(0,0,0,0.35);
    display: flex; align-items: center; justify-content: center; gap: 12px;
    font-size: 19px; color: var(--ink);
  }
  .name-pill .phone { font-size: 16px; font-weight: 700; }
  .postcard--back .brand { left: 398px; top: 34px; color: var(--ink); }
  .postcard--back .brand__mark { background: var(--ink); }
  .stamp-box {
    position: absolute; left: 618px; top: 27px; width: 86px; height: 86px;
    border: 1px solid #d0d0d0;
  }
</style>
</head>
<body>

<section class="postcard postcard--front">
  <div class="front__topbar"></div>
  <div class="front__photo" role="img" aria-label="Photo of a domed capitol building at the end of a tree-lined walkway under blue sky"></div>
  <div class="front__bottombar"></div>

  <div class="front__panel">
    <h1 class="front__headline">Let us help you save thousands on tution costs</h1>
    <div class="rule"></div>
    <p class="front__body">We have been helping out-of-state families gain Texas residency for over 14 years.</p>
    <p class="front__cta">LET US HELP YOU TOO.</p>
    <div class="phone-pill">
      <svg class="icon" viewBox="0 0 16 16" aria-hidden="true"><circle cx="8" cy="8" r="7" fill="none" stroke="#fff" stroke-width="1.4"/><path d="M5.4 4.6l1.3-.4.8 1.8-.9.7c.4.9 1 1.5 1.9 1.9l.7-.9 1.8.8-.4 1.3c-3 0-5.2-2.2-5.2-5.2z" fill="#fff"/></svg>
      <span>(555) 246-8013</span>
    </div>
    <p class="front__name">Mark Fenwick</p>
  </div>

  <div class="brand"><span class="brand__mark"></span><span>Harborline Realty</span></div>

  <div class="front__contacts">
    <span class="contact">
      <svg class="icon" viewBox="0 0 16 16" aria-hidden="true"><circle cx="8" cy="8" r="8" fill="#bbb"/><rect x="4" y="5" width="8" height="6" fill="none" stroke="#222" stroke-width="1.2"/><path d="M4 5l4 3 4-3" fill="none" stroke="#222" stroke-width="1.2"/></svg>
      mfenwick@harborlinerealty.com
    </span>
    <span class="contact">
      <svg class="icon" viewBox="0 0 16 16" aria-hidden="true"><circle cx="8" cy="8" r="8" fill="#bbb"/><circle cx="8" cy="8" r="4" fill="none" stroke="#222" stroke-width="1.2"/><path d="M4 8h8M8 4v8" stroke="#222" stroke-width="1"/></svg>
      www.harborlinerealty.com
    </span>
  </div>
</section>

<section class="postcard postcard--back">
  <div class="back__design">
    <div class="back__photo-student" role="img" aria-label="Photo of a student in a denim jacket carrying books"></div>
    <div class="back__photo-bridge" role="img" aria-label="Photo of an arched steel bridge over a river at sunset"></div>

    <div class="back__content">
      <p class="back__lead">Establishing Texas residency throught a property purchase is as easy as 1-2-3.</p>
      <div class="rule"></div>
      <p class="back__note">Contact us to learn how we have helped more than 500 families - and counting save thousands on tution.</p>
      <div class="back__contact-row">
        <span>Let us help you too.</span>
        <span class="contact email">
          <svg class="icon" viewBox="0 0 16 16" aria-hidden="true"><circle cx="8" cy="8" r="8" fill="#999"/><rect x="4" y="5" width="8" height="6" fill="none" stroke="#fff" stroke-width="1.2"/><path d="M4 5l4 3 4-3" fill="none" stroke="#fff" stroke-width="1.2"/></svg>
          mfenwick@harborlinerealty.com
        </span>
      </div>
    </div>

    <div class="back__footer">
      <p class="back__footer-web">www.harborlinerealty.com</p>
    </div>

    <div class="back__banner">
      Delvar parents, did you know<br>
      you can <span class="highlight">SAVE OVER $13,800</span><br>
      a semester in tuition?
    </div>

    <div class="name-pill">
      <span>Mark Fenwick</span>
      <svg class="icon" viewBox="0 0 16 16" aria-hidden="true"><circle cx="8" cy="8" r="7" fill="none" stroke="#111" stroke-width="1.4"/><path d="M5.4 4.6l1.3-.4.8 1.8-.9.7c.4.9 1 1.5 1.9 1.9l.7-.9 1.8.8-.4 1.3c-3 0-5.2-2.2-5.2-5.2z" fill="#111"/></svg>
      <span class="phone">(555) 246-8013</span>
    </div>
  </div>

  <div class="brand"><span class="brand__mark"></span><span>Harborline Realty</span></div>
  <div class="stamp-box"></div>
</section>

</body>
</html>
```